Kestrel Facilities Business Card Design

We would now like to design business cards with the new Kestrel Facilities logo

Target Market(s)

Professional

Industry/Entity Type

Professional services

Contact Information for Business Card

Employee name, title, phone number, email address, corporate office address and logo.

Font styles to use
Sans Serif

Colors
0054AA
0677BA
7BADD7
CADEEF
E8F1F8

Requirements
Must have
• My logo
Should not have
• any other pictures or images besides my logo

```html
<!DOCTYPE html>
<html lang="en">
<head>
<meta charset="utf-8">
<title>Kestrel Facilities – Business Card</title>
<link href="https://fonts.googleapis.com/css2?family=Oswald:wght@500&family=Lato:wght@400&display=swap" rel="stylesheet">
<style>
  :root {
    --brand-blue: #0680e8;
    --brand-blue-text: #1a82e6;
    --ink: #1d1d1d;
    --rule: #9a9a9a;
    --paper: #ffffff;
    --backdrop: #bdbdbd;
  }
  * { margin: 0; padding: 0; box-sizing: border-box; }
  html, body { width: 1200px; height: 1200px; overflow: hidden; }
  body { background: var(--backdrop); position: relative; font-family: "Lato", sans-serif; }

  .card { position: absolute; top: 303px; width: 368px; height: 594px; }
  .card-front { left: 200px; background: var(--brand-blue); }
  .card-back { left: 599px; background: var(--paper); text-align: center; }

  .brand { position: absolute; display: flex; align-items: center; gap: 14px;
           font-family: "Oswald", sans-serif; font-weight: 500; text-transform: uppercase; line-height: 1.04; }
  .brand-mark { width: 36px; height: 36px; flex: none; }
  .brand-name { font-size: 46px; letter-spacing: 1px; }

  .card-front .brand { left: 56px; top: 418px; color: var(--paper); }
  .card-front .brand-mark { background: var(--paper); }
  .card-back .brand { left: 58px; top: 115px; color: var(--brand-blue); text-align: left; }
  .card-back .brand-mark { background: var(--brand-blue); }

  .person-name { position: absolute; top: 322px; left: 0; right: 0;
                 font-family: "Oswald", sans-serif; font-weight: 500; font-size: 33px;
                 color: var(--brand-blue-text); text-transform: uppercase; letter-spacing: -0.8px; line-height: 1; }
  .person-title { position: absolute; top: 363px; left: 0; right: 0; font-size: 15.5px; color: var(--ink); letter-spacing: 0.3px; }

  .icon-row { position: absolute; top: 395px; left: 87px; width: 190px; height: 26px;
              display: flex; align-items: center; gap: 4px; }
  .icon-row .rule { flex: 1; height: 1px; background: var(--rule); }
  .icon-row .rule:first-child { margin-right: 2px; }
  .icon-row .rule:last-child { margin-left: 2px; }
  .contact-icon { width: 25px; height: 25px; background: var(--brand-blue); border-radius: 3px; display: block; }

  .contact-list { position: absolute; top: 431px; left: 0; right: 0; font-size: 18px; line-height: 21.7px; color: var(--ink); list-style: none; }
  .contact-list .accent { color: var(--brand-blue-text); }
  .divider { position: absolute; top: 507px; left: 88px; width: 195px; height: 1px; background: var(--rule); }
  .address { position: absolute; top: 517px; left: 0; right: 0; font-size: 18px; line-height: 21.7px; color: var(--ink); font-style: normal; }
</style>
</head>
<body>
  <section class="card card-front" aria-label="Card front">
    <div class="brand">
      <span class="brand-mark"></span>
      <span class="brand-name">Kestrel<br>Facilities</span>
    </div>
  </section>

  <section class="card card-back" aria-label="Card back">
    <div class="brand">
      <span class="brand-mark"></span>
      <span class="brand-name">Kestrel<br>Facilities</span>
    </div>

    <h1 class="person-name">Daniel Hartley</h1>
    <p class="person-title">MANAGING DIRECTOR</p>

    <div class="icon-row">
      <span class="rule"></span>
      <svg class="contact-icon" viewBox="0 0 25 25" aria-label="Phone">
        <rect width="25" height="25" rx="3" fill="#0680e8"/>
        <path d="M6 11c0-3 13-3 13 0v1.5h-3.5V11h-6v1.5H6z" fill="#fff"/>
        <rect x="8" y="13" width="9" height="6" rx="1" fill="#fff"/>
      </svg>
      <svg class="contact-icon" viewBox="0 0 25 25" aria-label="Email">
        <rect width="25" height="25" rx="3" fill="#0680e8"/>
        <rect x="5.5" y="8" width="14" height="9.5" fill="none" stroke="#fff" stroke-width="1.3"/>
        <path d="M5.5 8l7 5.5 7-5.5" fill="none" stroke="#fff" stroke-width="1.3"/>
      </svg>
      <svg class="contact-icon" viewBox="0 0 25 25" aria-label="Website">
        <rect width="25" height="25" rx="3" fill="#0680e8"/>
        <circle cx="12.5" cy="12.5" r="7" fill="none" stroke="#fff" stroke-width="1.4"/>
        <path d="M5.5 12.5h14M12.5 5.5c-3 3.5-3 10.5 0 14M12.5 5.5c3 3.5 3 10.5 0 14" fill="none" stroke="#fff" stroke-width="1.1"/>
      </svg>
      <span class="rule"></span>
    </div>

    <ul class="contact-list">
      <li>044-555 218 630</li>
      <li>info@kestrelfm.com</li>
      <li>www.<span class="accent">kestrelfm</span>.com</li>
    </ul>
    <div class="divider"></div>
    <address class="address">388, Harbour Lane<br>60217, Northland</address>
  </section>
</body>
</html>
```